Web Page Design for a Website that Provides Tutoring

I am looking to create an online tutoring website. The website will allow parents or students to contact tutors with a view to instructing them to tutor themselves or their children.

The name of the website is LendYourLessons.

This brief is to create the design for one of the web pages for this web site. I am hoping the same designer will be available to design other pages.

The page I want designed is one of the more complex and I have attached the design as an excel spreadsheet. The web page needs to include all the items on this page but if you want to change the positioning of the items then Im fine with that.

I recently had two logos created for this website. My favourite is the one with a mortar board but im not sure I like the colours. I have attached both of these logos and you can use either of them, change the colours or create something different. I just want a design pleasing to the eye. If the logo is changed I would like that in a seperate file.

So can you please submit designs for this page. I have attached the two logos which you can use, change or if you feel you have a better idea then you can use that.

On the spreadsheet the Send Message, Favourite etc are buttons.

Target Market(s)

People who want to better themselves.
Possible middle class to upper class.

Industry/Entity Type

Tutoring

Number of Pages Required

1 page

Requirements
Must have
• The designs must have alot of the information attached in the spreadsheet.

```html
<!DOCTYPE html>
<html lang="en">
<head>
<meta charset="utf-8">
<title>LendYourLessons – Tutor Profile</title>
<link rel="stylesheet" href="https://fonts.googleapis.com/css2?family=Montserrat:wght@400;500;600;700&family=Open+Sans:wght@400;600&family=Roboto:wght@400;500&display=swap">
<style>
:root{
  --blue:#16a8e9;
  --blue-dark:#0a7fb8;
  --orange:#f7941d;
  --red:#ef6b4f;
  --green:#8cc63f;
  --grey:#d6d6d6;
  --grey-soft:#f6f6f6;
  --yellow:#fdbf10;
  --text:#444;
  --text-light:#777;
  --footer:#2a2b2e;
  --white:#fff;
}
*{box-sizing:border-box;margin:0;padding:0}
html,body{width:1200px;height:3340px;overflow:hidden}
body{position:relative;background:var(--white);font-family:"Open Sans",Arial,sans-serif;color:var(--text)}
.abs{position:absolute}
.heading{font-family:"Montserrat",Arial,sans-serif;font-weight:700;color:var(--blue);font-size:24px}

/* hero */
.hero{position:absolute;left:0;top:0;width:1200px;height:508px;background:linear-gradient(120deg,#5b4a3e 0%,#8b7a6a 35%,#6f7f86 65%,#3e4b52 100%)}
.hero-shade{position:absolute;inset:0;background:rgba(20,25,30,.45)}
.logo{font-family:"Montserrat",Arial,sans-serif;font-weight:700;color:var(--white);font-size:24px;letter-spacing:-.3px}
.logo-mark{display:inline-block;width:14px;height:14px;background:var(--orange);margin-right:6px;vertical-align:1px}
.nav{position:absolute;top:29px;left:400px;font-family:"Montserrat",Arial,sans-serif;font-size:9.5px;font-weight:600;color:var(--white)}
.nav a{color:var(--white);text-decoration:none;position:absolute;white-space:nowrap}
.nav a.active{color:var(--orange)}
.topbar{position:absolute;top:28px;font-family:"Montserrat",Arial,sans-serif;font-size:9.5px;font-weight:600;color:var(--white);white-space:nowrap}
.welcome{position:absolute;top:137px;width:1200px;text-align:center;font-family:"Montserrat",sans-serif;font-weight:700;color:var(--white);font-size:12px;letter-spacing:.5px}
.hero-title{position:absolute;top:155px;width:1200px;text-align:center;font-family:"Montserrat",sans-serif;font-weight:700;font-size:34px;color:var(--white);letter-spacing:-.5px}
.hero-title span{color:var(--orange)}
.tile{position:absolute;top:223px;width:160px;height:171px;background:var(--blue);color:var(--white);font-family:"Montserrat",sans-serif;font-weight:700;font-size:11px;text-align:center}
.tile.active{background:var(--orange);height:173px}
.tile svg{position:absolute;left:54px;top:38px;width:52px;height:52px}
.tile span{position:absolute;top:103px;left:0;width:100%}
.dots{position:absolute;top:459px;left:580px;display:flex;gap:5px}
.dots i{width:9px;height:9px;border-radius:50%;border:1.5px solid var(--white)}
.dots i.on{background:var(--green);border-color:var(--green)}

/* profile */
.photo{position:absolute;left:67px;top:568px;width:349px;height:350px;background:radial-gradient(circle at 50% 45%,#bdbdbd 0%,#8a8a8a 45%,#4a4a4a 100%)}
.score{position:absolute;left:67px;font-size:17px;color:var(--text);width:350px}
.score .stars{position:absolute;left:147px;top:0}
.score .val{position:absolute;left:278px;top:0}
.stars{color:var(--orange);font-size:16px;letter-spacing:0}
.stars .off{color:#cfcfcf}
.info-box{position:absolute;left:503px;top:568px;width:617px;height:345px;border:1px solid #e2e2e2;box-shadow:0 1px 4px rgba(0,0,0,.12);background:var(--white)}
.info-head{height:71px;background:var(--blue);color:var(--white);font-family:"Montserrat",sans-serif;font-weight:700;font-size:23px;padding:22px 0 0 28px}
.info-field{position:absolute;font-family:"Montserrat",sans-serif;font-size:17px;color:var(--text)}
.info-text{position:absolute;left:27px;top:266px;width:560px;font-size:14px;line-height:21px;color:var(--text-light)}
.action{position:absolute;top:918px;width:44px;height:44px;background:var(--blue)}
.action svg{position:absolute;left:11px;top:11px;width:22px;height:22px}

/* fact cards */
.fact{position:absolute;height:55px;background:var(--white);box-shadow:0 1px 4px rgba(0,0,0,.18);font-family:"Montserrat",sans-serif;text-align:center}
.fact::before{content:"";position:absolute;left:0;top:0;width:24px;height:50%;background:var(--blue)}
.fact::after{content:"";position:absolute;left:0;bottom:0;width:24px;height:50%;background:var(--orange)}
.fact b{position:absolute;left:24px;right:0;top:6px;font-weight:500;font-size:13px;color:var(--blue)}
.fact em{position:absolute;left:24px;right:0;top:30px;font-style:normal;font-size:13px;color:var(--text)}

/* subjects */
.band-grey{position:absolute;left:0;top:1276px;width:1200px;height:383px;background:var(--grey-soft)}
.table{position:absolute;left:67px;top:1376px;width:1053px;table-layout:fixed;border-collapse:collapse;background:var(--white);box-shadow:0 1px 4px rgba(0,0,0,.12);font-family:"Montserrat",sans-serif;font-size:17px}
.table th,.table td{height:59px;text-align:center;font-weight:400;color:var(--text);border-bottom:1px solid #e6e6e6;white-space:nowrap}
.table th{height:60px}
.table th.shade{background:#c4c4c4;color:var(--white)}
.table td.subject{color:var(--white);font-weight:500}
.table td.bio{background:var(--blue)}
.table td.chem{background:var(--yellow)}

/* availability */
.calendar{position:absolute;left:67px;top:1757px;width:423px;height:363px;background:var(--white);box-shadow:0 1px 5px rgba(0,0,0,.16);font-family:"Roboto",sans-serif}
.cal-month{position:absolute;left:20px;top:22px;font-size:23px;color:#222}
.cal-month::after{content:"";display:inline-block;margin-left:12px;border:7px solid transparent;border-top-color:#999;vertical-align:-3px}
.cal-grid{position:absolute;left:16px;top:68px;display:grid;grid-template-columns:repeat(7,56px);grid-auto-rows:47px;font-size:15px;color:#333}
.cal-grid span{display:flex;align-items:center;justify-content:center}
.cal-grid .dow{font-weight:500;font-size:16px;height:32px}
.cal-grid span i{font-style:normal;width:34px;height:34px;border-radius:50%;display:flex;align-items:center;justify-content:center}
.cal-grid .b{font-weight:500;color:#000}
.cal-grid .taken i{background:var(--red);color:var(--white)}
.cal-grid .res i{background:var(--orange);color:var(--white)}
.cal-grid .av i{background:var(--green);color:var(--white)}
.cal-grid .no i{background:var(--grey);color:var(--white)}
.cal-grid .ring i{border:1.5px solid #ddd}
.legend{position:absolute;left:775px;font-family:"Montserrat",sans-serif;font-size:18px;color:var(--text)}
.legend i{position:absolute;left:0;top:0;width:77px;height:23px}
.legend span{position:absolute;left:107px;top:-1px}

/* reviews */
.reviews{position:absolute;left:0;top:2211px;width:1200px;height:312px;background:var(--blue);color:var(--white);text-align:center}
.quote-mark{position:absolute;left:249px;top:0;font-family:"Montserrat",sans-serif;font-weight:700;font-size:230px;line-height:170px;color:var(--blue-dark);height:84px;overflow:hidden}
.reviews h2{position:absolute;top:48px;width:100%;font-family:"Montserrat",sans-serif;font-weight:700;font-size:23px}
.avatars{position:absolute;top:94px;left:540px;display:flex;gap:8px;align-items:center}
.avatar{border-radius:50%;border:3px solid rgba(255,255,255,.7)}
.reviews p{position:absolute;left:312px;top:150px;width:578px;font-size:11.5px;line-height:19px}
.reviews .next{position:absolute;left:876px;top:194px;font-size:24px;color:rgba(255,255,255,.6)}
.reviews .dash{position:absolute;left:592px;top:235px;width:14px;height:2px;background:var(--white)}
.reviews .who{position:absolute;top:245px;width:100%;font-family:"Montserrat",sans-serif;font-weight:700;font-size:10px}
.reviews .rstars{position:absolute;top:260px;width:100%;font-size:19px;color:var(--orange)}
.reviews .rstars .off{color:var(--white)}

/* feedback */
.feedback{position:absolute;left:67px;top:2612px;width:1053px;height:310px;background:var(--white);box-shadow:0 1px 5px rgba(0,0,0,.16)}
.feedback h2{position:absolute;left:15px;top:17px}
.feedback .rule{position:absolute;left:0;top:62px;width:100%;height:1px;background:#e3e3e3}
.fb-row{position:absolute;left:0;width:1053px;height:54px;background:var(--white);box-shadow:0 1px 3px rgba(0,0,0,.14);border-left:6px solid var(--blue)}
.fb-row.alt{border-left-color:var(--yellow)}
.fb-row .avatar{position:absolute;left:17px;top:8px;width:40px;height:40px;border:0}
.fb-name{position:absolute;left:102px;top:7px;font-family:"Montserrat",sans-serif;font-weight:600;font-size:9px;line-height:12px;color:#333}
.fb-name small{display:block;font-weight:400;font-size:9px}
.fb-row .stars{position:absolute;left:102px;top:30px;font-size:14px}
.fb-row p{position:absolute;left:202px;top:7px;width:823px;font-size:9px;line-height:13px;color:var(--text-light)}

/* footer */
.footer{position:absolute;left:0;top:3022px;width:1200px;height:318px;background:var(--footer);color:#bbb}
.footer .logo{position:absolute;left:263px;top:55px;font-size:19px}
.footer h3{position:absolute;top:55px;font-family:"Montserrat",sans-serif;font-weight:600;font-size:12px;color:var(--white)}
.footer ul{position:absolute;left:490px;top:84px;list-style:none;font-family:"Montserrat",sans-serif;font-size:9.5px;line-height:18.3px;color:#ccc}
.footer .news-text{position:absolute;left:728px;top:82px;width:230px;font-size:10px;line-height:16px}
.footer .email{position:absolute;left:728px;top:137px;width:218px;height:32px;border-radius:16px;background:#3b3c40;font-size:9px;color:#888;padding:10px 0 0 24px;font-family:"Montserrat",sans-serif}
.footer .subscribe{position:absolute;left:858px;top:137px;width:88px;height:32px;border-radius:16px;background:var(--blue);color:var(--white);font-family:"Montserrat",sans-serif;font-weight:700;font-size:10px;text-align:center;line-height:32px}
.footer .copy{position:absolute;left:252px;top:276px;font-size:9px;color:#888}
.footer .social{position:absolute;top:276px;font-family:"Montserrat",sans-serif;font-size:8.5px;font-weight:500;color:var(--blue)}
.footer .social.alt{color:var(--red)}
</style>
</head>
<body>

<header class="hero" role="img" aria-label="Photo of smiling students studying together around a table">
  <div class="hero-shade"></div>
</header>

<div class="logo abs" style="left:129px;top:16px"><span class="logo-mark"></span>LendYourLessons</div>
<nav class="nav">
  <a style="left:0">HOME</a>
  <a class="active" style="left:47px">SEARCH</a>
  <a style="left:105px">STUDENT</a>
  <a style="left:168px">TUTOR</a>
  <a style="left:219px">ABOUT</a>
  <a style="left:268px">CONTACT</a>
</nav>
<svg class="abs" style="left:811px;top:29px" width="10" height="12" viewBox="0 0 10 12"><path d="M2 1l2 3-1 1c1 2 2 3 3 4l1-1 3 2-1 2C5 12 0 6 0 3z" fill="#fff"/></svg>
<div class="topbar" style="left:824px">+00 5550 1234 000</div>
<svg class="abs" style="left:928px;top:24px" width="18" height="18" viewBox="0 0 18 18"><circle cx="9" cy="9" r="9" fill="var(--blue)"/><path d="M5 7h8v5H5z" fill="none" stroke="#fff" stroke-width="1.2"/></svg>
<div class="topbar" style="left:976px">LOGIN</div>
<svg class="abs" style="left:1023px;top:21px" width="14" height="22" viewBox="0 0 14 22"><rect x="1" y="1" width="12" height="20" fill="none" stroke="#fff" stroke-width="1.3"/><path d="M4 11h6M8 8l3 3-3 3" fill="none" stroke="#fff" stroke-width="1.3"/></svg>
<div class="topbar" style="left:1049px">REGISTER</div>
<svg class="abs" style="left:1107px;top:21px" width="22" height="22" viewBox="0 0 22 22"><circle cx="11" cy="7" r="5" fill="none" stroke="#fff" stroke-width="1.3"/><path d="M2 21c1-6 5-8 9-8s8 2 9 8" fill="none" stroke="#fff" stroke-width="1.3"/></svg>

<div class="welcome">WELCOME TO</div>
<div class="hero-title"><span>LEND</span> YOUR LESSONS</div>

<div class="tile" style="left:69px"><svg viewBox="0 0 52 52" fill="none" stroke="#fff" stroke-width="2"><path d="M6 26L26 8l20 18M12 21v23h10V32h8v12h10V21"/></svg><span>HOME</span></div>
<div class="tile active" style="left:247px"><svg viewBox="0 0 52 52" fill="none" stroke="#fff" stroke-width="2"><circle cx="22" cy="22" r="14"/><circle cx="22" cy="22" r="9"/><path d="M32 32l14 14"/></svg><span>SEARCH</span></div>
<div class="tile" style="left:425px"><svg viewBox="0 0 52 52" fill="none" stroke="#fff" stroke-width="2"><path d="M2 20l24-10 24 10-24 10z"/><path d="M12 25v12c8 6 20 6 28 0V25M44 22v14"/></svg><span>STUDENT</span></div>
<div class="tile" style="left:603px"><svg viewBox="0 0 52 52" fill="none" stroke="#fff" stroke-width="2"><rect x="4" y="4" width="44" height="32"/><circle cx="16" cy="40" r="4"/><path d="M8 50c1-5 4-7 8-7s7 2 8 7M22 36l14-14M30 14l4 6 8-8"/></svg><span>TUTOR</span></div>
<div class="tile" style="left:781px"><svg viewBox="0 0 52 52" fill="none" stroke="#fff" stroke-width="2"><rect x="6" y="8" width="40" height="10"/><rect x="8" y="18" width="36" height="12"/><rect x="4" y="30" width="44" height="14"/><path d="M10 13h28M12 24h24M10 37h32"/></svg><span>ABOUT</span></div>
<div class="tile" style="left:959px"><svg viewBox="0 0 52 52" fill="none" stroke="#fff" stroke-width="2"><path d="M12 6l8 10-4 4c3 6 8 11 14 14l4-4 10 8-6 8C18 44 6 30 6 14z"/><path d="M30 6a16 16 0 0 1 16 16M30 13a9 9 0 0 1 9 9"/></svg><span>CONTACT</span></div>

<div class="dots"><i class="on"></i><i></i><i></i></div>

<!-- profile -->
<div class="photo" role="img" aria-label="Black and white portrait photo of the tutor"></div>
<div class="score" style="top:928px">Review Score:<span class="stars">★★★★<span class="off">★</span></span><span class="val">4.5 / 5.0</span></div>
<div class="score" style="top:954px">Reliability:<span class="stars">★★★★<span class="off">★</span></span><span class="val">4.0 / 5.0</span></div>
<div class="score" style="top:980px">Punctuality:<span class="stars">★★★★<span class="off">★</span></span><span class="val">4.6 / 5.0</span></div>

<section class="info-box">
  <div class="info-head">TUTOR INFORMATION</div>
  <div class="info-field" style="left:27px;top:98px">Name :</div>
  <div class="info-field" style="left:334px;top:98px">Experience :</div>
  <div class="info-field" style="left:27px;top:151px">Age &amp; Gender :</div>
  <div class="info-field" style="left:334px;top:151px">Qualification :</div>
  <div class="info-field" style="left:27px;top:218px">City :</div>
  <p class="info-text">Lorem ipsum dolor sit amet, consectetur adipisicing elit, sed do eiusmod tempor incididunt ut labore et dolore magna aliqua. Ut enim ad minim veniam, quis nostrud exercitation ullamco laboris nisi ut aliquip ex ea</p>
</section>
<div class="action" style="left:978px" aria-label="Send message"><svg viewBox="0 0 22 22"><rect x="2" y="5" width="18" height="12" fill="#fff"/><path d="M2 5l9 7 9-7" fill="none" stroke="var(--blue)" stroke-width="1.5"/></svg></div>
<div class="action" style="left:1027px" aria-label="Favourite"><svg viewBox="0 0 22 22"><path d="M11 19L3 11a4.5 4.5 0 0 1 8-5 4.5 4.5 0 0 1 8 5z" fill="#fff"/></svg></div>
<div class="action" style="left:1076px" aria-label="Write review"><svg viewBox="0 0 22 22" fill="none" stroke="#fff" stroke-width="1.8"><path d="M4 18l1-5L15 3l4 4L9 17zM13 5l4 4"/></svg></div>

<div class="fact" style="left:67px;top:1085px;width:240px"><b>Tutoring Type</b><em>In personal only</em></div>
<div class="fact" style="left:339px;top:1085px;width:240px"><b>Willing To Travel</b><em>Home Only</em></div>
<div class="fact" style="left:610px;top:1085px;width:243px"><b>Age</b><em>20</em></div>
<div class="fact" style="left:880px;top:1085px;width:240px"><b>DBS (CRB)</b></div>
<div class="fact" style="left:67px;top:1163px;width:240px"><b>Teacher</b></div>
<div class="fact" style="left:339px;top:1163px;width:240px"><b>Full Time Tutor</b></div>
<div class="fact" style="left:610px;top:1163px;width:243px"><b>Full Time Student</b></div>

<!-- subjects -->
<section class="band-grey"></section>
<h2 class="heading abs" style="left:67px;top:1327px">SUBJECTS TAUGHT</h2>
<table class="table">
  <colgroup><col style="width:189px"><col style="width:145px"><col style="width:143px"><col style="width:145px"><col style="width:141px"><col style="width:147px"><col style="width:143px"></colgroup>
  <tr><th></th><th class="shade">Primary</th><th>Secondary</th><th class="shade">GCSE</th><th>A-Level</th><th class="shade">University</th><th>Adult Learner</th></tr>
  <tr><td class="subject bio">Biology</td><td>£20</td><td></td><td>£25</td><td>£30</td><td></td><td></td></tr>
  <tr><td class="subject chem">Chemistry</td><td>£20</td><td></td><td>£25</td><td>£30</td><td></td><td></td></tr>
</table>

<!-- availability -->
<h2 class="heading abs" style="left:67px;top:1699px">AVAILABILITY</h2>
<section class="calendar">
  <div class="cal-month">November</div>
  <div class="cal-grid">
    <span class="dow">M</span><span class="dow">T</span><span class="dow">W</span><span class="dow">T</span><span class="dow">F</span><span class="dow">S</span><span class="dow">S</span>
    <span></span><span></span><span></span><span></span><span></span><span class="ring"><i>1</i></span><span><i>2</i></span>
    <span><i>3</i></span><span class="b"><i>4</i></span><span class="taken"><i>5</i></span><span class="ring"><i>6</i></span><span class="taken"><i>7</i></span><span><i>8</i></span><span><i>9</i></span>
    <span><i>10</i></span><span class="b"><i>11</i></span><span><i>12</i></span><span><i>13</i></span><span class="av"><i>14</i></span><span class="no"><i>15</i></span><span class="taken"><i>16</i></span>
    <span class="res"><i>17</i></span><span class="b"><i>18</i></span><span class="taken"><i>19</i></span><span class="res"><i>20</i></span><span><i>21</i></span><span><i>22</i></span><span class="av"><i>23</i></span>
    <span class="av"><i>24</i></span><span class="b"><i>25</i></span><span><i>26</i></span><span class="ring"><i>27</i></span><span><i>28</i></span><span class="no"><i>29</i></span><span><i>30</i></span>
  </div>
</section>
<div class="legend" style="top:1911px"><i style="background:var(--red)"></i><span>Taken</span></div>
<div class="legend" style="top:1952px"><i style="background:var(--orange)"></i><span>Reserved</span></div>
<div class="legend" style="top:1992px"><i style="background:var(--green)"></i><span>Available</span></div>
<div class="legend" style="top:2029px"><i style="background:var(--grey)"></i><span>No</span></div>

<!-- reviews -->
<section class="reviews">
  <div class="quote-mark">“</div>
  <h2>TUTOR'S REVIEWS</h2>
  <div class="avatars">
    <div class="avatar" role="img" aria-label="Reviewer photo" style="width:34px;height:34px;background:#9fd3ea"></div>
    <div class="avatar" role="img" aria-label="Reviewer photo" style="width:44px;height:44px;background:#c07a4e"></div>
    <div class="avatar" role="img" aria-label="Reviewer photo" style="width:34px;height:34px;background:#9fd3ea"></div>
  </div>
  <p>Sam is a patient and encouraging tutor who makes hard ideas feel simple. Every lesson is well planned, and he always checks that I have understood before moving on. Since we started working together my confidence has grown and my grades have improved in both biology and chemistry.</p>
  <div class="next">»</div>
  <div class="dash"></div>
  <div class="who">STUDENT NAME</div>
  <div class="rstars">★★★★<span class="off">★</span></div>
</section>

<!-- feedback -->
<section class="feedback">
  <h2 class="heading">FEEDBACK</h2>
  <div class="rule"></div>
  <div class="fb-row" style="top:70px"><div class="avatar" role="img" aria-label="Parent photo" style="background:#8a6a52"></div><div class="fb-name">SAM CARTER<small>12/5/2016</small></div><div class="stars">★★★★<span class="off">★</span></div><p>Sam explained every topic with patience and care, and my son now enjoys biology for the first time. Lessons always started on time and each one ended with clear notes and a short task to practise at home. We have already booked another full term of weekly sessions with him.</p></div>
  <div class="fb-row alt" style="top:131px"><div class="avatar" role="img" aria-label="Parent photo" style="background:#6b6b6b"></div><div class="fb-name">SAM CARTER<small>12/5/2016</small></div><div class="stars">★★★★<span class="off">★</span></div><p>A calm and friendly tutor who quickly found the gaps in my daughter's chemistry. Her marks rose by two grades in one term, and she feels far more confident before tests. Sam also sent short progress updates after every lesson, which we found very helpful as parents.</p></div>
  <div class="fb-row" style="top:192px"><div class="avatar" role="img" aria-label="Parent photo" style="background:#a88a70"></div><div class="fb-name">SAM CARTER<small>12/5/2016</small></div><div class="stars">★★★★<span class="off">★</span></div><p>Very well prepared for each session, with past papers and worked examples ready to go. He adapts the pace to the student and never rushes a difficult idea. My son says the lessons are the clearest part of his week, and his exam results agree with him.</p></div>
  <div class="fb-row alt" style="top:253px"><div class="avatar" role="img" aria-label="Parent photo" style="background:#c9a184"></div><div class="fb-name">SAM CARTER<small>12/5/2016</small></div><div class="stars">★★★★<span class="off">★</span></div><p>Reliable, punctual and easy to talk to. Sam helped me revise for my university entry exams and showed me better ways to plan my study time. I would gladly recommend him to any student who wants steady support and honest feedback on their progress through the year.</p></div>
</section>

<!-- footer -->
<footer class="footer">
  <div class="logo"><span class="logo-mark"></span>LendYourLessons</div>
  <h3 style="left:490px">NAVIGATION</h3>
  <ul><li>HOME</li><li>SEARCH</li><li>STUDENT</li><li>TUTOR</li><li>ABOUT</li><li>CONTACT</li></ul>
  <h3 style="left:728px">NEWS LETTER</h3>
  <p class="news-text">Enter your email address to subscribe and be told of new posts and features by email.</p>
  <div class="email">EMAIL ADDRESS</div>
  <div class="subscribe">SUBSCRIBE</div>
  <div class="copy">Copyright © 2018 LendYourLessons</div>
  <div class="social" style="left:635px">KINFOLD</div>
  <div class="social" style="left:704px">CHIRPER</div>
  <div class="social" style="left:766px">SNAPFRAME</div>
  <div class="social" style="left:840px">LINKWORK</div>
  <div class="social alt" style="left:904px">CIRCLES</div>
</footer>

</body>
</html>
```